Birchline Septic Solutions

Would like to see some single sided ones but would also like to see some double sided with one sided only being the logo. Owners name is Colin Vandro. Phone number is 555-214-0387
Services are pumping, inspections, installs, and repairs

Contact Information for Business Card

555-241-0387 Colin Vandro Harlow Creek, OH

```html
<!DOCTYPE html>
<html lang="en">
<head>
<meta charset="utf-8">
<title>Birchline Septic Solutions — Business Cards</title>
<link href="https://fonts.googleapis.com/css2?family=Montserrat:wght@500;600;800&display=swap" rel="stylesheet">
<style>
  :root {
    --bg: #c9c9c9;
    --ink: #111111;
    --card-dark: #0b0b0b;
    --card-light: #ffffff;
    --teal: #2bb8ae;
    --scenery-dark: #1c1c1c;
    --scenery-light: #f1f1f1;
  }
  * { box-sizing: border-box; margin: 0; padding: 0; }
  html, body { width: 1200px; height: 900px; overflow: hidden; }
  body {
    background: var(--bg);
    font-family: "Montserrat", Arial, sans-serif;
    display: flex;
    flex-direction: column;
    align-items: center;
    justify-content: center;
    gap: 36px;
  }
  .card {
    position: relative;
    width: 700px;
    height: 400px;
    border-radius: 34px;
    overflow: hidden;
  }
  .card--front { background: var(--card-dark); color: #fff; }
  .card--back { background: var(--card-light); color: var(--ink); }

  .scenery {
    position: absolute;
    right: 0; top: 0;
    width: 62%; height: 100%;
  }
  .card--front .scenery { background: linear-gradient(120deg, transparent 20%, var(--scenery-dark) 70%, transparent 100%); }
  .card--back .scenery { background: linear-gradient(120deg, transparent 20%, var(--scenery-light) 70%, transparent 100%); }

  .brand {
    position: absolute;
    display: flex;
    align-items: center;
    gap: 14px;
    font-weight: 800;
    text-transform: uppercase;
    line-height: 1.05;
  }
  .brand__mark { width: 18px; height: 18px; background: var(--teal); flex: none; }
  .brand__name { font-size: 40px; letter-spacing: 1px; }
  .card--front .brand { left: 50%; top: 50%; transform: translate(-50%, -50%); }
  .card--back .brand { left: 60px; top: 70px; }

  .contact { position: absolute; left: 60px; bottom: 56px; }
  .contact__name { font-size: 30px; font-weight: 800; text-transform: uppercase; margin-bottom: 18px; }
  .contact__row { display: flex; align-items: center; gap: 14px; font-size: 22px; font-weight: 500; margin-top: 8px; }
  .contact__row svg { width: 20px; height: 20px; fill: var(--teal); flex: none; }

  .services { position: absolute; right: 50px; top: 150px; list-style: none; text-align: right; }
  .services li { font-size: 17px; font-weight: 500; text-transform: uppercase; line-height: 1.3; }
  .services li::after {
    content: ""; display: inline-block; width: 8px; height: 8px;
    background: var(--teal); margin-left: 8px; vertical-align: middle;
  }
</style>
</head>
<body>
  <section class="card card--front">
    <div class="scenery" role="img" aria-label="Faint mountain and pine forest backdrop"></div>
    <div class="brand">
      <span class="brand__mark"></span>
      <span class="brand__name">Birchline<br>Septic Solutions</span>
    </div>
  </section>

  <section class="card card--back">
    <div class="scenery" role="img" aria-label="Faint mountain and pine forest backdrop"></div>
    <div class="brand">
      <span class="brand__mark"></span>
      <span class="brand__name">Birchline<br>Septic Solutions</span>
    </div>
    <ul class="services">
      <li>Pumping</li>
      <li>Inspections</li>
      <li>Installs</li>
      <li>Repairs</li>
    </ul>
    <div class="contact">
      <p class="contact__name">Colin Vandro</p>
      <p class="contact__row">
        <svg viewBox="0 0 24 24" aria-hidden="true"><path d="M6.6 10.8a15.1 15.1 0 0 0 6.6 6.6l2.2-2.2a1 1 0 0 1 1-.25 11.4 11.4 0 0 0 3.6.57 1 1 0 0 1 1 1V20a1 1 0 0 1-1 1A17 17 0 0 1 3 4a1 1 0 0 1 1-1h3.5a1 1 0 0 1 1 1c0 1.25.2 2.45.57 3.57a1 1 0 0 1-.25 1z"/></svg>
        555-214-0387
      </p>
      <p class="contact__row">
        <svg viewBox="0 0 24 24" aria-hidden="true"><path d="M12 2a7 7 0 0 0-7 7c0 5.25 7 13 7 13s7-7.75 7-13a7 7 0 0 0-7-7zm0 9.5A2.5 2.5 0 1 1 12 6.5a2.5 2.5 0 0 1 0 5z"/></svg>
        Harlow Creek, OH
      </p>
    </div>
  </section>
</body>
</html>
```